Specialised investor in e-mobility and energy wants business card design

We need a business card design that fits our existing corporate design. <The look and feel must be 'sharp'/'clean', dynamic, communicate momentum, professionalism etc (as one would imagine from a firm in the financial sector). We like the idea of a reverse-side of the card that includes the logo, and the name and contact details on the other. We expect the deliverable to be whatever format might be required to be able to get cards printed directly by a service such as kelmo press. Our website is www.zub.capital

```html
<!DOCTYPE html>
<html lang="en">
<head>
<meta charset="utf-8">
<title>ZUB Capital – Business Card</title>
<link rel="stylesheet" href="https://fonts.googleapis.com/css2?family=Montserrat:wght@400;500;700&display=swap">
<style>
  :root {
    --backdrop: #1f1f1f;
    --card-green: #344f24;
    --accent-green: #86b64a;
    --text-white: #ffffff;
  }
  * { margin: 0; padding: 0; box-sizing: border-box; }
  html, body {
    width: 1200px;
    height: 1059px;
    overflow: hidden;
    background: var(--backdrop);
    font-family: "Montserrat", Arial, sans-serif;
    color: var(--text-white);
  }
  .card {
    position: absolute;
    width: 690px;
    height: 392px;
    background: var(--card-green);
    border-radius: 20px;
  }
  .card--front { left: 256px; top: 89px; }
  .card--back { left: 255px; top: 547px; }

  .brand-name {
    position: absolute;
    font-weight: 500;
    color: var(--text-white);
    white-space: nowrap;
    letter-spacing: 0.5px;
  }
  .card--front .brand-name {
    right: 42px;
    top: 48px;
    font-size: 44px;
  }
  .card--back .brand-name {
    left: 0;
    right: 0;
    text-align: center;
    top: 142px;
    font-size: 86px;
  }

  .holder {
    position: absolute;
    left: 41px;
    top: 190px;
  }
  .holder__name {
    font-size: 26px;
    font-weight: 700;
    color: var(--accent-green);
    line-height: 1.1;
  }
  .holder__title {
    font-size: 15.5px;
    font-weight: 400;
    line-height: 1.2;
    margin-top: 2px;
  }

  .divider {
    position: absolute;
    left: 40px;
    right: 40px;
    top: 257px;
    height: 1px;
    background: var(--accent-green);
  }

  .contact-list {
    position: absolute;
    left: 40px;
    top: 275px;
    list-style: none;
  }
  .contact-list__item {
    display: flex;
    align-items: center;
    gap: 7px;
    font-size: 16px;
    height: 27.5px;
  }
  .contact-list__icon {
    width: 12px;
    height: 12px;
    fill: var(--accent-green);
    flex: none;
  }

  .address {
    position: absolute;
    right: 40px;
    top: 306px;
    text-align: right;
    font-style: normal;
    font-size: 16px;
    line-height: 22px;
  }
</style>
</head>
<body>

<section class="card card--front" aria-label="Business card front">
  <div class="brand-name">ZUB Capital</div>

  <div class="holder">
    <div class="holder__name">Martin Keller</div>
    <div class="holder__title">Director/Founder</div>
  </div>

  <div class="divider"></div>

  <ul class="contact-list">
    <li class="contact-list__item">
      <svg class="contact-list__icon" viewBox="0 0 24 24" aria-hidden="true">
        <path d="M6.6 10.8a15.1 15.1 0 0 0 6.6 6.6l2.2-2.2c.3-.3.7-.4 1-.2 1.1.4 2.3.6 3.6.6.6 0 1 .4 1 1V20c0 .6-.4 1-1 1C10.6 21 3 13.4 3 4c0-.6.4-1 1-1h3.5c.6 0 1 .4 1 1 0 1.3.2 2.5.6 3.6.1.3 0 .7-.2 1z"/>
      </svg>
      <span>123-480-2391</span>
    </li>
    <li class="contact-list__item">
      <svg class="contact-list__icon" viewBox="0 0 24 24" aria-hidden="true">
        <path d="M2 5h20v14H2z M2 6l10 7 10-7" />
      </svg>
      <span>info@zub.capital</span>
    </li>
    <li class="contact-list__item">
      <svg class="contact-list__icon" viewBox="0 0 24 24" aria-hidden="true">
        <circle cx="12" cy="12" r="10"/>
      </svg>
      <span>www.zub.capital</span>
    </li>
  </ul>

  <address class="address">
    1234 Street Name<br>
    Country Name AB 5748
  </address>
</section>

<section class="card card--back" aria-label="Business card back">
  <div class="brand-name">ZUB Capital</div>
</section>

</body>
</html>
```